A business card design for a dental office. We have Two doctors working here. We practice general de

I already have a logo designed for the office with the name and a slogan.
Now I need to create design for a business card using the same logo.
Details Needed on the front side of the card are :
Bernard K. Oswin, DDS
Gerald M Fenwick, DDS
418 Birch Lane
Portland, CT 00000
Phone : 555 019 4831
Fax : 555 019 4832
Website : WWW.BrightmoorToothHaven.Com
Office hours by appointment
On the back side of the card need :
Appointment
Date....................Time...................
With....................................
If unable to keep your appointment, please give 24-48 hours notice in order to avoid broken appointment fee.

Industry/Entity Type

Dental Clinic

Contact Information for Business Card

Bernard K. Oswin, DDS
Gerald M Fenwick, DDS
418 Birch Lane
Portland, CT 00000
Phone : 555 019 4831
Fax : 555 019 4832
Appointment

Requirements
Must have
• Keep the Name and slogan on the logo on the front of the card. You can move them around the Logo and Name/Slogan of business (Oswin Family Dentistry/Gentle care for every smile) as you wish to get a feel of the design.
• Bernard K. Oswin, DDS
• Gerald M Fenwick, DDS
• 418 Birch Lane
• Portland, CT 00000
• Phone : 555 019 4831
• Fax : 555 019 4832
• WWW.BrightmoorToothHaven.Com
• Keep these three groups above as they are together now in different areas of the front side.
• On the back side of the card need :
• Appointment
• Date....................Time...................
• With....................................
• If unable to keep your appointment, please give 24-48 hours notice in order to avoid broken appointment fee.

```html
<!DOCTYPE html>
<html lang="en">
<head>
<meta charset="utf-8">
<title>Oswin Family Dentistry – Business Card</title>
<link href="https://fonts.googleapis.com/css2?family=Open+Sans:wght@400;600;700&display=swap" rel="stylesheet">
<style>
  :root {
    --backdrop: #2b2b2d;
    --card-dark: #1c1c1e;
    --card-light: #ffffff;
    --accent-red: #e2222b;
    --accent-blue: #1f4fa0;
    --text-light: #f2f2f2;
    --divider: #3a3a3d;
    --mark-ring: #1f6fb0;
  }
  * { box-sizing: border-box; margin: 0; padding: 0; }
  html, body { width: 1200px; height: 900px; overflow: hidden; }
  body {
    background: var(--backdrop);
    font-family: "Open Sans", Arial, sans-serif;
    position: relative;
  }
  .card {
    position: absolute;
    top: 295px;
    width: 540px;
    height: 310px;
    border-radius: 22px;
    overflow: hidden;
  }
  /* Front side */
  .card-front { left: 40px; background: var(--card-dark); color: var(--text-light); }
  .front-brand {
    position: absolute; left: 34px; top: 70px; width: 190px;
    display: flex; flex-direction: column; align-items: center; gap: 14px;
  }
  .brand-dot {
    width: 120px; height: 120px; border-radius: 50%;
    background: var(--mark-ring);
  }
  .brand-name {
    font-weight: 700; font-size: 17px; line-height: 1.25; text-align: center;
    color: var(--text-light);
  }
  .front-divider {
    position: absolute; left: 250px; top: 40px; width: 1px; height: 200px;
    background: var(--divider);
  }
  .front-details { position: absolute; left: 272px; top: 42px; }
  .doctor { color: var(--accent-red); font-weight: 600; font-size: 19px; line-height: 1.15; }
  .address { margin-top: 22px; font-size: 14px; line-height: 1.5; }
  .address span { display: block; }
  .address .city { padding-left: 12px; }
  .contact-list { list-style: none; margin-top: 14px; font-size: 14px; line-height: 1.6; }
  .contact-list li { display: flex; align-items: center; gap: 9px; }
  .contact-list svg { width: 12px; height: 12px; flex: none; fill: var(--accent-red); }

  /* Back side */
  .card-back { left: 620px; background: var(--card-light); }
  .back-brand {
    position: absolute; left: 28px; top: 26px;
    display: flex; align-items: center; gap: 14px;
  }
  .back-brand .brand-dot { width: 70px; height: 70px; }
  .brand-lockup { display: flex; flex-direction: column; align-items: flex-start; }
  .brand-title { color: var(--accent-blue); font-weight: 700; font-size: 19px; letter-spacing: 0.5px; }
  .brand-slogan {
    margin-top: 3px; color: var(--accent-red); font-size: 8px; letter-spacing: 1px;
    display: flex; align-items: center; gap: 6px;
  }
  .brand-slogan::before, .brand-slogan::after {
    content: ""; width: 26px; height: 1px; background: var(--accent-red);
  }
  .appointment-title {
    position: absolute; left: 0; right: 0; top: 112px; text-align: center;
    color: var(--accent-red); font-weight: 600; font-size: 19px;
  }
  .appointment-fields { position: absolute; left: 40px; right: 40px; top: 150px; }
  .field-row { display: flex; align-items: flex-end; gap: 10px; margin-bottom: 14px; }
  .field-label { color: var(--accent-red); font-weight: 600; font-size: 16px; }
  .field-line { flex: 1; border-bottom: 2px dotted var(--accent-blue); margin-bottom: 5px; }
  .notice {
    position: absolute; left: 30px; right: 30px; top: 236px;
    text-align: center; font-weight: 700; font-size: 13px; line-height: 1.5;
  }
  .notice .red { color: var(--accent-red); }
  .notice .blue { color: var(--accent-blue); }
</style>
</head>
<body>
  <section class="card card-front" aria-label="Card front">
    <div class="front-brand">
      <div class="brand-dot"></div>
      <div class="brand-name">Oswin Family Dentistry</div>
    </div>
    <div class="front-divider"></div>
    <div class="front-details">
      <p class="doctor">Bernard K. Oswin, DDS</p>
      <p class="doctor">Gerald M Fenwick, DDS</p>
      <p class="address"><span>418 Birch Lane</span><span class="city">Millbrook, VT 00000</span></p>
      <ul class="contact-list">
        <li><svg viewBox="0 0 24 24"><path d="M6.6 10.8a15.1 15.1 0 0 0 6.6 6.6l2.2-2.2a1 1 0 0 1 1-.25 11.4 11.4 0 0 0 3.6.57 1 1 0 0 1 1 1V20a1 1 0 0 1-1 1A17 17 0 0 1 3 4a1 1 0 0 1 1-1h3.5a1 1 0 0 1 1 1c0 1.25.2 2.45.57 3.57a1 1 0 0 1-.25 1z"/></svg>555 019 4831</li>
        <li><svg viewBox="0 0 24 24"><path d="M6 2h10v5H6zM3 8h18v10h-3v4H6v-4H3zm5 7v5h8v-5z"/></svg>555 019 4832</li>
        <li><svg viewBox="0 0 24 24"><circle cx="12" cy="12" r="10"/></svg>WWW.BrightmoorToothHaven.Com</li>
        <li class="hours">Office hours by appointment</li>
      </ul>
    </div>
  </section>

  <section class="card card-back" aria-label="Card back">
    <div class="back-brand">
      <div class="brand-dot"></div>
      <div class="brand-lockup">
        <span class="brand-title">OSWIN FAMILY DENTISTRY</span>
        <span class="brand-slogan">GENTLE CARE FOR EVERY SMILE</span>
      </div>
    </div>
    <h2 class="appointment-title">Appointment</h2>
    <div class="appointment-fields">
      <div class="field-row">
        <span class="field-label">Date</span><span class="field-line"></span>
        <span class="field-label">Time</span><span class="field-line"></span>
      </div>
      <div class="field-row">
        <span class="field-label">With</span><span class="field-line"></span>
      </div>
    </div>
    <p class="notice">
      <span class="red">If unable to keep your appointment, please give 24-48 hours</span><br>
      <span class="blue">notice in order to avoid broken appointment fee.</span>
    </p>
  </section>
</body>
</html>
```